Business Card Design Project

This is the first time we use our new logo. We need a business card that we can use both on our institutional corporate relationships and also that works for our staff that deals with consumers directly.

VELUNDA is a new company dedicated to empower consumers and to provide them with the best choices for specialized health care using the latest telemedicine technology (medicine at a distance via videoconference).

We want to print this cards in high quality materials and process. We will like designs that allow us to use UV spot varnish and other techniques that will differentiate us.

We are including Two different versions of Color logos. In addition we are including white over black background logos. Those can be used replacing the black for a color.

Please note this is the first time we will be creating any corporate materials with our new logo and colors.

Target Market(s)

34+ consumers of medium high and high socioeconomic levels.

Industry/Entity Type

Health

Requirements
Must have
• Our logo on its original colors
Should not have
• Any other graphical element or design that is not our logo

```html
<!DOCTYPE html>
<html lang="en">
<head>
<meta charset="utf-8">
<title>VELUNDA Business Card</title>
<link rel="stylesheet" href="https://fonts.googleapis.com/css2?family=Montserrat:wght@500;700&family=Arimo:wght@400&display=swap">
<style>
  :root {
    --page-bg: #e9eaec;
    --card-top: #2b2b2c;
    --card-bottom: #121213;
    --brand-blue: #1f6cb0;
    --name-blue: #2b8fd6;
    --title-teal: #17a596;
    --sky-blue: #4fb0e6;
    --contact-white: #f2f2f2;
    --rule-silver: #b9bcc0;
  }
  * { box-sizing: border-box; margin: 0; padding: 0; }
  html, body { width: 1200px; height: 987px; overflow: hidden; }
  body { background: var(--page-bg); position: relative; font-family: "Arimo", Arial, sans-serif; }

  .card {
    position: absolute;
    width: 580px;
    height: 332px;
    border-radius: 34px;
    background: linear-gradient(160deg, var(--card-top), var(--card-bottom));
    box-shadow: 0 18px 40px rgba(0,0,0,0.22);
    overflow: hidden;
  }
  .card--back { left: 570px; top: 100px; }
  .card--front { left: 50px; top: 540px; }

  /* back side */
  .back-brand {
    position: absolute; left: 0; right: 0; top: 110px;
    display: flex; align-items: center; justify-content: center; gap: 16px;
  }
  .brand-dot { width: 30px; height: 30px; border-radius: 50%; background: var(--brand-blue); }
  .brand-name {
    font-family: "Montserrat", sans-serif; font-weight: 700;
    color: var(--brand-blue); letter-spacing: 3px;
  }
  .back-brand .brand-name { font-size: 46px; }
  .back-url {
    position: absolute; left: 0; right: 0; top: 200px; text-align: center;
    font-size: 18px; letter-spacing: 4px; color: var(--sky-blue);
  }

  /* front side */
  .front-brand {
    position: absolute; left: 46px; top: 44px;
    display: flex; align-items: center; gap: 14px;
  }
  .front-brand .brand-dot { width: 24px; height: 24px; }
  .front-brand .brand-name { font-size: 40px; }
  .divider {
    position: absolute; left: 40px; right: 40px; top: 128px; height: 1px;
    background: linear-gradient(90deg, transparent, var(--rule-silver) 15%, var(--rule-silver) 85%, transparent);
  }
  .person {
    position: absolute; left: 46px; top: 146px;
    font-family: "Montserrat", sans-serif; font-weight: 500; font-size: 24px;
    color: var(--name-blue);
  }
  .person .title { color: var(--title-teal); font-size: 18px; }
  .contacts {
    position: absolute; left: 46px; top: 196px;
    color: var(--contact-white); font-size: 16px; line-height: 28px;
  }
  .contact-row { display: flex; align-items: center; gap: 6px; }
  .contact-row .sep { width: 12px; }
  .icon { width: 14px; height: 14px; fill: var(--contact-white); flex: none; }
</style>
</head>
<body>
  <section class="card card--back" aria-label="Card back">
    <div class="back-brand">
      <span class="brand-dot"></span>
      <span class="brand-name">VELUNDA</span>
    </div>
    <p class="back-url">www.velunda.com</p>
  </section>

  <section class="card card--front" aria-label="Card front">
    <div class="front-brand">
      <span class="brand-dot"></span>
      <span class="brand-name">VELUNDA</span>
    </div>
    <div class="divider"></div>
    <p class="person">Your Name, <span class="title">Title</span></p>
    <div class="contacts">
      <div class="contact-row">
        <svg class="icon" viewBox="0 0 16 16"><path d="M3.5 1.5l2.5 0 1 3.5-1.6 1.2a8 8 0 0 0 4.4 4.4l1.2-1.6 3.5 1v2.5c0 .8-.7 1.5-1.5 1.5A12 12 0 0 1 2 3c0-.8.7-1.5 1.5-1.5z"/></svg>
        <span>012-345-6789</span><span class="sep"></span>
        <svg class="icon" viewBox="0 0 16 16"><path d="M3.5 1.5l2.5 0 1 3.5-1.6 1.2a8 8 0 0 0 4.4 4.4l1.2-1.6 3.5 1v2.5c0 .8-.7 1.5-1.5 1.5A12 12 0 0 1 2 3c0-.8.7-1.5 1.5-1.5z"/></svg>
        <span>012-345-6789</span>
      </div>
      <div class="contact-row">
        <svg class="icon" viewBox="0 0 16 16"><path d="M1 4h14v9H1z M1 4l7 5 7-5" fill="none" stroke="#f2f2f2" stroke-width="1.5"/></svg>
        <span>name@velunda.com</span><span class="sep"></span>
        <svg class="icon" viewBox="0 0 16 16"><circle cx="8" cy="8" r="6.5" fill="none" stroke="#f2f2f2" stroke-width="1.3"/><path d="M1.5 8h13M8 1.5c-3 3.5-3 9.5 0 13M8 1.5c3 3.5 3 9.5 0 13" fill="none" stroke="#f2f2f2" stroke-width="1"/></svg>
        <span>www.velunda.com</span>
      </div>
      <div class="contact-row">
        <span>Street Name, City Name, State, City Zip Code</span>
      </div>
    </div>
  </section>
</body>
</html>
```